Web Design Project for a new download application :-)

We need a website design and a logo design for a new website and desktop application.
The Website will be www.Gruvlo.com
The installed application will be: Gruvlo

Gruvlo is a desktop application that searches and finds all kind of Media files (Movies, Games, Songs, software, etc..)
Gruvlo will also manage the download process for the selected files.
Gruvlo automates the whole search and download process.

User Flow:
users will initially visit the website.
user will download the application from the website
user will install the application on his computer.
user will run and use the application.

What makes our software special:
-Great search engine for searching media files.
-Very high speed downloads. maximum speeds.
-Allow used to Search by: file type, size, date, format
-Pause and resume downloads
-Get any file you want instantly.
-Unlimited Downloads.

We will need:
Logo
WebSite Design
Icons for the desktop application.

we need only PSDs - no codded pages are needed !

Design to the following screen Size & resolution: 1024 x 768

Target Market(s)

movies and music lovers.
users who download movies, games, softwares, music etc...

Industry/Entity Type

Software

Requirements
Must have
• must have download button

```html
<!DOCTYPE html>
<html lang="en">
<head>
<meta charset="utf-8">
<title>Gruvlo – Download all kind of media files</title>
<link href="https://fonts.googleapis.com/css2?family=Ubuntu:wght@400;500;700&family=Open+Sans:wght@400;600&display=swap" rel="stylesheet">
<style>
:root{
  --navy:#0b2a45;
  --navy-deep:#061c30;
  --sky:#1e9be0;
  --sky-light:#5cc4f2;
  --ink:#0d2238;
  --feature-blue:#1b78c6;
  --body-grey:#666a6e;
  --page:#f3f3f3;
  --orange:#f7941d;
  --white:#ffffff;
  --footer:#2aa0dc;
}
*{margin:0;padding:0;box-sizing:border-box}
html,body{width:1200px;height:1037px;overflow:hidden}
body{position:relative;background:var(--page);font-family:"Open Sans",Arial,sans-serif;color:var(--body-grey)}
.rainbow{position:absolute;left:0;top:0;width:1200px;height:5px;background:linear-gradient(90deg,#e6332a,#f7a21b,#ffe100,#4cb848,#1ea1e0,#8e44ad,#e6332a,#f7a21b)}
.topbar{position:absolute;left:0;top:5px;width:1200px;height:85px;background:linear-gradient(180deg,var(--navy) 0%,var(--navy-deep) 100%)}
.brand{position:absolute;font-family:"Ubuntu",sans-serif;font-weight:700;color:var(--white);letter-spacing:-1px;white-space:nowrap}
.brand-top{left:114px;top:4px;font-size:72px;line-height:78px}
.nav{position:absolute;top:26px;left:527px;display:flex;align-items:center;font-family:"Ubuntu",sans-serif;font-size:17px;font-weight:500}
.nav a{color:var(--white);text-decoration:none;margin-right:17px}
.nav .current{position:relative;background:linear-gradient(#ffffff,#d8d8d8);color:#111;padding:5px 9px;border-radius:2px}
.nav .current::after{content:"";position:absolute;left:26px;bottom:-7px;border:7px solid transparent;border-bottom:0;border-top-color:#d8d8d8}
.lang{position:absolute;left:918px;top:31px;display:flex;align-items:center;font-size:12px;color:var(--white)}
.lang .select{margin-left:6px;width:75px;height:21px;background:var(--white);color:#333;padding:2px 5px;position:relative}
.lang .select::after{content:"";position:absolute;right:6px;top:8px;border:4px solid transparent;border-top-color:#222;border-bottom:0}
.hero{position:absolute;left:0;top:90px;width:1200px;height:325px;background:radial-gradient(ellipse at 70% 30%,var(--sky-light) 0%,var(--sky) 45%,#0f76c2 100%)}
.device-monitor{position:absolute;left:116px;top:121px;width:375px;height:318px;border-radius:10px;background:linear-gradient(170deg,#2b2f35,#15181c 70%,#c9ccd0 100%)}
.device-laptop{position:absolute;left:398px;top:262px;width:240px;height:158px;border-radius:6px;background:linear-gradient(170deg,#2b2f35,#101317)}
.device-laptop-base{position:absolute;left:358px;top:416px;width:320px;height:20px;border-radius:0 0 12px 12px;background:linear-gradient(#e6e7e9,#a9acb0)}
.hero-title{position:absolute;left:654px;top:128px;font-family:"Ubuntu",sans-serif;font-weight:700;color:var(--white);font-size:74px;line-height:84px;letter-spacing:-2px}
.hero-sub{position:absolute;left:657px;top:206px;font-family:"Ubuntu",sans-serif;font-weight:700;color:var(--white);font-size:34px;line-height:40px}
.hero-list{position:absolute;left:659px;top:244px;font-family:"Ubuntu",sans-serif;color:var(--ink);font-size:26px;line-height:30px}
.download-btn{position:absolute;left:660px;top:284px;width:326px;height:74px;border-radius:3px;background:linear-gradient(#ffdd3a,#fbb117 60%,#f59a12);box-shadow:0 2px 4px rgba(0,0,0,.3);font-family:"Ubuntu",sans-serif;font-weight:700;font-size:31px;color:#1a1a1a;display:flex;align-items:center;justify-content:center;text-decoration:none}
.ribbon{position:absolute;left:112px;top:458px;width:240px;height:58px}
.ribbon svg{display:block}
.ribbon span{position:absolute;left:22px;top:2px;font-family:"Ubuntu",sans-serif;color:var(--white);font-size:35px}
.feature{position:absolute;top:522px;width:210px;text-align:center}
.feature .icon{display:block;width:70px;height:68px;margin:0 auto 7px}
.feature h3{font-family:"Ubuntu",sans-serif;font-weight:400;color:var(--feature-blue);font-size:18px;line-height:22px;margin-bottom:6px}
.feature p{font-size:12.5px;line-height:18px;padding:0 8px}
.divider{position:absolute;top:530px;width:1px;height:210px;background:linear-gradient(transparent,#dcdcdc,transparent)}
.arrow{position:absolute;top:620px}
.rule{position:absolute;left:210px;top:764px;width:820px;height:1px;background:linear-gradient(90deg,transparent,#d5d5d5,transparent)}
.quote-mark{position:absolute;font-family:Georgia,serif;font-weight:700;color:#b8b8b8;font-size:90px;line-height:90px}
.quote-open{left:115px;top:768px}
.quote-close{left:1050px;top:852px}
.testimonial{position:absolute;left:177px;top:797px;width:875px;font-size:12.3px;line-height:18px;color:#555}
.cite{position:absolute;left:179px;top:876px;font-family:Arial,sans-serif;font-size:12px;color:#222}
.cite .name{color:var(--orange)}
.footer{position:absolute;left:0;top:937px;width:1200px;height:100px;background:linear-gradient(var(--footer),#2496d3)}
.footer-nav{position:absolute;left:124px;top:28px;font-size:12px}
.footer-nav a{color:var(--white);margin-right:15px}
.footer-contact{position:absolute;left:124px;top:54px;font-size:14px;color:var(--white)}
.footer-contact a{color:var(--white)}
.footer-contact small{font-size:12px}
.brand-footer{left:924px;top:18px;font-size:58px;line-height:62px}
</style>
</head>
<body>
<div class="rainbow"></div>
<header class="topbar">
  <div class="brand brand-top">Gruvlo</div>
  <nav class="nav">
    <a class="current" href="#">HOME</a>
    <a href="#">DOWNLOAD</a>
    <a href="#">SUPPORT</a>
    <a href="#">AFFILIATES</a>
  </nav>
  <div class="lang">Select Language <div class="select">English</div></div>
</header>

<section class="hero"></section>
<div class="device-monitor" role="img" aria-label="Desktop monitor showing the Gruvlo application browsing a folder of photos"></div>
<div class="device-laptop" role="img" aria-label="Laptop screen showing the Gruvlo application"></div>
<div class="device-laptop-base"></div>
<h1 class="hero-title">DOWNLOAD</h1>
<div class="hero-sub">ALL KIND OF MEDIA FILES</div>
<div class="hero-list">Movies, Games, Songs, Software, etc.</div>
<a class="download-btn" href="#">DOWNLOAD Gruvlo</a>

<div class="ribbon">
  <svg width="240" height="58" viewBox="0 0 240 58">
    <defs><linearGradient id="rib" x1="0" x2="1"><stop offset="0" stop-color="#f7941d"/><stop offset="1" stop-color="#ffc20e"/></linearGradient></defs>
    <polygon points="0,0 228,0 240,25 228,50 0,50" fill="url(#rib)"/>
    <polygon points="0,50 10,50 10,57" fill="#c46a0a"/>
  </svg>
  <span>Features</span>
</div>

<svg class="arrow" style="left:116px" width="22" height="30" viewBox="0 0 22 30"><polyline points="18,3 5,15 18,27" fill="none" stroke="#111" stroke-width="6"/></svg>
<svg class="arrow" style="left:1066px" width="22" height="30" viewBox="0 0 22 30"><polyline points="4,3 17,15 4,27" fill="none" stroke="#111" stroke-width="6"/></svg>

<div class="feature" style="left:149px">
  <div class="icon" role="img" aria-label="Magnifying glass over a film strip" style="background:radial-gradient(circle at 45% 40%,#a9d6f5,#6a8aa8 60%,#e9a23b)"></div>
  <h3>Great Search Engine for Searching Media Files</h3>
  <p>Lorem ipsum dolor sit amet, consectetur adipiscing elit. Sed mollis, ante placerat placerat varius, elit ante varius quam, sit amet dignissim purus urna vel</p>
</div>
<div class="divider" style="left:371px"></div>
<div class="feature" style="left:383px">
  <svg class="icon" viewBox="0 0 70 68"><circle cx="35" cy="33" r="31" fill="#f0f0f0"/><circle cx="35" cy="33" r="26" fill="#f47a12"/><path d="M31 17h8v16h8L35 47 23 33h8z" fill="#fff"/></svg>
  <h3>Very High Speed Downloads</h3>
  <p>Curabitur convallis lectus quis tellus suscipit sollicitudin. Phasellus suscipit justo sit amet nisl rhoncus congue. Integer non egestas nibh.</p>
</div>
<div class="divider" style="left:604px"></div>
<div class="feature" style="left:616px">
  <div class="icon" role="img" aria-label="Document with a green download arrow" style="background:linear-gradient(135deg,#eef0f2 55%,#6cc04a)"></div>
  <h3>Search by: file type, size, date, format</h3>
  <p>Nulla vitae imperdiet elit. Quisque vehicula, nulla sit amet ultrices molestie, purus tortor consequat magna, et eleifend elit quam</p>
</div>
<div class="divider" style="left:837px"></div>
<div class="feature" style="left:848px">
  <svg class="icon" viewBox="0 0 70 68"><circle cx="35" cy="29" r="24" fill="#1a3fa8"/><rect x="27" y="19" width="6" height="20" fill="#fff"/><rect x="37" y="19" width="6" height="20" fill="#fff"/></svg>
  <h3>Pause and Resume Downloads</h3>
  <p>Mauris eu quam sit amet sem suscipit rhoncus. Ut mauris dolor, bibendum at lacinia sit amet, dictum a justo. Aliquam ac est nunc, in suscipit libero.</p>
</div>

<div class="rule"></div>
<div class="quote-mark quote-open">“</div>
<p class="testimonial">Aenean nunc dui, varius vitae auctor eu, tincidunt adipiscing sem. Praesent massa nibh, imperdiet eget luctus vel, suscipit sit amet augue. Donec risus lacus, luctus nec condimentum non, venenatis eu risus. Vestibulum lorem nunc, placerat nec blandit at, mollis a justo. In faucibus lacus a magna congue id auctor lectus tristique. Aenean imperdiet bibendum est, ut accumsan neque bibendum quis. Quisque non enim eget lacus hendrerit faucibus. Nullam est erat, posuere vitae sodales</p>
<div class="cite"><span class="name">Dan Harper</span> &nbsp;|&nbsp; Perth</div>
<div class="quote-mark quote-close">”</div>

<footer class="footer">
  <nav class="footer-nav">
    <a href="#">HOME</a> <a href="#">DOWNLOAD</a><a href="#">SUPPORT</a><a href="#">AFFILIATES</a>
  </nav>
  <div class="footer-contact">email : <a href="#">contact@gruvlo.com</a> &nbsp;| &nbsp;Call us - 0198765432 &nbsp;| &nbsp;<small>©2011 Gruvlo. All rights reserved</small></div>
  <div class="brand brand-footer">Gruvlo</div>
</footer>
</body>
</html>
```